Brookmere Osteopathy flyer

I want a clean clear DL flyer (but also want an A4 poster) promoting a new Osteopathic business in a semi rural area in Tasmania (Australia).
It can have pictures like the examples attached to show people what Osteopathy is (its like Chiropractic and physiotherapy).
I am the sole practioner and am male, so any pictures would be best to be a white male if possible.
I've attached some wording, you can use all, or none of it
I don't have a phone number for the business yet
info@brookmereosteopathy.example
www.brookmereosteopathy.example
Target Market(s)
Australians, from tradies, professionals, babies to retired people
Industry/Entity Type
Health
Look and feel

```html
<!DOCTYPE html>
<html lang="en">
<head>
<meta charset="utf-8">
<title>Brookmere Osteopathy – Flyer</title>
<link rel="stylesheet" href="https://fonts.googleapis.com/css2?family=Montserrat:wght@700&family=Rubik:wght@400&family=Roboto+Condensed:wght@700&display=swap">
<style>
  :root{
    --frame:#c3c3c3;
    --paper:#ffffff;
    --blue:#229fdb;
    --blue-head:#1e96d6;
    --orange:#f7943a;
    --ink:#2b2b2b;
    --list-ink:#333333;
  }
  html,body{margin:0;padding:0;overflow:hidden;}
  body{width:819px;height:1200px;background:var(--frame);position:relative;}
  .flyer{position:absolute;left:36px;top:40px;width:747px;height:1119px;background:var(--paper);overflow:hidden;}
  .art{position:absolute;left:-36px;top:-40px;width:819px;height:1200px;}
  .brand{position:absolute;left:562px;top:16px;width:157px;height:157px;border:2px solid var(--blue);border-radius:50%;
    box-sizing:border-box;display:flex;align-items:center;justify-content:center;text-align:center;
    font-family:"Montserrat",sans-serif;font-weight:700;font-size:15px;line-height:1.3;color:var(--blue);letter-spacing:.5px;}
  .reasons-title{position:absolute;left:361px;top:608px;margin:0;font-family:"Montserrat",sans-serif;font-weight:700;
    font-size:24px;line-height:40px;color:var(--blue-head);letter-spacing:0;}
  .reasons{position:absolute;left:362px;top:702px;margin:0;padding:0;list-style:none;font-family:"Rubik",sans-serif;
    font-size:21.5px;color:var(--list-ink);}
  .reasons li{height:37.2px;display:flex;align-items:center;gap:12px;white-space:nowrap;}
  .reasons svg{width:28px;height:28px;flex:none;}
  .reasons small{font-size:15px;}
  .intro{position:absolute;left:32px;top:757px;width:310px;margin:0;font-family:"Roboto Condensed",sans-serif;font-weight:700;
    font-size:22.5px;line-height:31px;color:var(--ink);letter-spacing:-.2px;}
  .contact{position:absolute;left:32px;top:999px;margin:0;padding:0;list-style:none;font-family:"Rubik",sans-serif;
    font-size:17px;color:#fff;}
  .contact li{display:flex;align-items:center;gap:8px;height:25.5px;white-space:nowrap;}
  .contact svg{width:20px;height:20px;flex:none;}
</style>
</head>
<body>
<main class="flyer">
  <svg class="art" viewBox="0 0 819 1200">
    <defs>
      <linearGradient id="g-neck" x1="0" y1="0" x2="1" y2="1">
        <stop offset="0" stop-color="#f2f2f3"/>
        <stop offset=".35" stop-color="#ebe8e6"/>
        <stop offset=".6" stop-color="#dcc6b8"/>
        <stop offset=".8" stop-color="#c9a089"/>
        <stop offset="1" stop-color="#3e3735"/>
      </linearGradient>
      <linearGradient id="g-back" x1="0" y1="0" x2="0" y2="1">
        <stop offset="0" stop-color="#f4f1ee"/>
        <stop offset=".22" stop-color="#ead2c1"/>
        <stop offset=".5" stop-color="#dcae8f"/>
        <stop offset=".75" stop-color="#d9a887"/>
        <stop offset=".88" stop-color="#f1efef"/>
        <stop offset="1" stop-color="#f7f7f8"/>
      </linearGradient>
      <linearGradient id="g-baby" x1="0" y1="0" x2="0" y2="1">
        <stop offset="0" stop-color="#b3b0c6"/>
        <stop offset=".25" stop-color="#d8b7a6"/>
        <stop offset=".5" stop-color="#e1c0ae"/>
        <stop offset=".62" stop-color="#58afe0"/>
        <stop offset=".8" stop-color="#4aa3d8"/>
        <stop offset="1" stop-color="#a6b9d9"/>
      </linearGradient>
    </defs>
    <path class="photo-neck" role="img" aria-label="Photo: male osteopath treating the neck of a woman lying on a treatment table"
      fill="url(#g-neck)" d="M62,110 Q62,62 110,62 L382,62 C490,62 575,150 596,250 L596,550 L160,550 C100,520 62,440 62,360 Z"/>
    <path class="photo-back" role="img" aria-label="Photo: osteopath's hands working on a patient's lower back"
      fill="url(#g-back)" stroke="#fff" stroke-width="8" d="M410,340 C410,290 450,252 510,252 L712,252 Q750,252 750,290 L750,520 C750,575 705,615 650,615 L450,615 Q410,615 410,575 Z"/>
    <path class="photo-baby" role="img" aria-label="Photo: gentle hands cradling a sleeping baby's head"
      fill="url(#g-baby)" stroke="#fff" stroke-width="8" d="M93,545 C93,515 140,493 190,493 L320,493 Q346,493 346,520 L346,680 C346,730 300,763 240,763 L125,763 Q93,763 93,730 Z"/>
    <rect class="accent-bar" x="400" y="1130" width="383" height="29" fill="var(--orange)"/>
    <path class="contact-band" fill="var(--blue)" d="M36,1011 L280,1011 C340,1011 375,1040 390,1080 L418,1159 L36,1159 Z"/>
  </svg>

  <div class="brand">Brookmere<br>Osteopathy</div>

  <h2 class="reasons-title">COMMON REASONS PEOPLE<br>VISIT AN OSTEOPATH</h2>

  <ul class="reasons">
    <li><svg viewBox="0 0 28 28"><circle cx="14" cy="14" r="12.5" fill="none" stroke="var(--orange)" stroke-width="1.6"/><circle cx="14" cy="14" r="8" fill="none" stroke="var(--orange)" stroke-width="1.2"/><path d="M14 10 L18 14 L14 18 L10 14 Z" fill="var(--orange)"/></svg>Back / neck pain</li>
    <li><svg viewBox="0 0 28 28"><circle cx="14" cy="14" r="12.5" fill="none" stroke="var(--orange)" stroke-width="1.6"/><circle cx="14" cy="14" r="8" fill="none" stroke="var(--orange)" stroke-width="1.2"/><path d="M14 10 L18 14 L14 18 L10 14 Z" fill="var(--orange)"/></svg>Headaches / migraines</li>
    <li><svg viewBox="0 0 28 28"><circle cx="14" cy="14" r="12.5" fill="none" stroke="var(--orange)" stroke-width="1.6"/><circle cx="14" cy="14" r="8" fill="none" stroke="var(--orange)" stroke-width="1.2"/><path d="M14 10 L18 14 L14 18 L10 14 Z" fill="var(--orange)"/></svg>Joint and muscle pain</li>
    <li><svg viewBox="0 0 28 28"><circle cx="14" cy="14" r="12.5" fill="none" stroke="var(--orange)" stroke-width="1.6"/><circle cx="14" cy="14" r="8" fill="none" stroke="var(--orange)" stroke-width="1.2"/><path d="M14 10 L18 14 L14 18 L10 14 Z" fill="var(--orange)"/></svg>Pregnancy-related discomfort</li>
    <li><svg viewBox="0 0 28 28"><circle cx="14" cy="14" r="12.5" fill="none" stroke="var(--orange)" stroke-width="1.6"/><circle cx="14" cy="14" r="8" fill="none" stroke="var(--orange)" stroke-width="1.2"/><path d="M14 10 L18 14 L14 18 L10 14 Z" fill="var(--orange)"/></svg>Disc related issues</li>
    <li><svg viewBox="0 0 28 28"><circle cx="14" cy="14" r="12.5" fill="none" stroke="var(--orange)" stroke-width="1.6"/><circle cx="14" cy="14" r="8" fill="none" stroke="var(--orange)" stroke-width="1.2"/><path d="M14 10 L18 14 L14 18 L10 14 Z" fill="var(--orange)"/></svg>Sciatica</li>
    <li><svg viewBox="0 0 28 28"><circle cx="14" cy="14" r="12.5" fill="none" stroke="var(--orange)" stroke-width="1.6"/><circle cx="14" cy="14" r="8" fill="none" stroke="var(--orange)" stroke-width="1.2"/><path d="M14 10 L18 14 L14 18 L10 14 Z" fill="var(--orange)"/></svg>Plantar fasciitis</li>
    <li><svg viewBox="0 0 28 28"><circle cx="14" cy="14" r="12.5" fill="none" stroke="var(--orange)" stroke-width="1.6"/><circle cx="14" cy="14" r="8" fill="none" stroke="var(--orange)" stroke-width="1.2"/><path d="M14 10 L18 14 L14 18 L10 14 Z" fill="var(--orange)"/></svg>Tendonitis / Bursitis</li>
    <li><svg viewBox="0 0 28 28"><circle cx="14" cy="14" r="12.5" fill="none" stroke="var(--orange)" stroke-width="1.6"/><circle cx="14" cy="14" r="8" fill="none" stroke="var(--orange)" stroke-width="1.2"/><path d="M14 10 L18 14 L14 18 L10 14 Z" fill="var(--orange)"/></svg><span>Adhesive capsulitis <small>(frozen shoulder)</small></span></li>
    <li><svg viewBox="0 0 28 28"><circle cx="14" cy="14" r="12.5" fill="none" stroke="var(--orange)" stroke-width="1.6"/><circle cx="14" cy="14" r="8" fill="none" stroke="var(--orange)" stroke-width="1.2"/><path d="M14 10 L18 14 L14 18 L10 14 Z" fill="var(--orange)"/></svg>Tennis / Golfers elbow</li>
  </ul>

  <p class="intro">Osteopaths use a combination of joint manipulation, targeted deep tissue massage and stretching to improve function relieve pain and support the body’s ability to heal itself.</p>

  <ul class="contact">
    <li><svg viewBox="0 0 20 20"><circle cx="10" cy="10" r="9" fill="none" stroke="#fff" stroke-width="1.3"/><path d="M10 4.5a3.3 3.3 0 0 1 3.3 3.3C13.3 10.3 10 15 10 15S6.7 10.3 6.7 7.8A3.3 3.3 0 0 1 10 4.5z" fill="none" stroke="#fff" stroke-width="1.3"/><circle cx="10" cy="7.8" r="1.2" fill="#fff"/></svg>48 Ridgeline Road, Brookmere</li>
    <li><svg viewBox="0 0 20 20"><circle cx="10" cy="10" r="9" fill="none" stroke="#fff" stroke-width="1.3"/><path d="M6.5 5.5l2 .2.8 2.2-1.2 1a6 6 0 0 0 3 3l1-1.2 2.2.8.2 2c-.5.6-1.3.9-2 .8-3.5-.5-6.2-3.2-6.7-6.7-.1-.7.2-1.5.7-2.1z" fill="none" stroke="#fff" stroke-width="1.2"/></svg>&nbsp;xxxx xxx xxx</li>
    <li><svg viewBox="0 0 20 20"><circle cx="10" cy="10" r="9" fill="none" stroke="#fff" stroke-width="1.3"/><circle cx="10" cy="10" r="5.2" fill="none" stroke="#fff" stroke-width="1.1"/><path d="M4.8 10h10.4M10 4.8c-2 2.8-2 7.6 0 10.4M10 4.8c2 2.8 2 7.6 0 10.4" fill="none" stroke="#fff" stroke-width="1"/></svg>www.brookmereosteopathy.example</li>
    <li><svg viewBox="0 0 20 20"><circle cx="10" cy="10" r="9" fill="none" stroke="#fff" stroke-width="1.3"/><rect x="5" y="6.5" width="10" height="7" fill="none" stroke="#fff" stroke-width="1.2"/><path d="M5 6.5l5 4 5-4" fill="none" stroke="#fff" stroke-width="1.2"/></svg>info@brookmereosteopathy.example</li>
  </ul>
</main>
</body>
</html>
```